Single Webpage Custom Design

We need a single webpage design (no coding) that uses our color and design scheme (http://insight.veltomarsafe.com/).
We attached a draft that outlines the structure and content of what the page should look like.
As shown in the draft we need the following sections (in that order):
- Graphic with Text & Logo on top
- Product Explanation
- Customer Logos
- Success Stories with logo and citation each
- Contact form
- Footer

```html
<!DOCTYPE html>
<html lang="en">
<head>
<meta charset="utf-8">
<title>Veltomar – Human Firewall</title>
<link href="https://fonts.googleapis.com/css2?family=Montserrat:wght@300;400;500;600;700;800&display=swap" rel="stylesheet">
<style>
:root{
  --teal:#21b3bb;
  --teal-light:#2fc3ca;
  --teal-dark:#16888f;
  --orange:#f59c1e;
  --navy:#1f3340;
  --text:#4a5560;
  --muted:#8a949c;
  --line:#d9e3e6;
  --white:#ffffff;
  --footer-bar:#eeeeee;
}
*{box-sizing:border-box;margin:0;padding:0}
html,body{width:1200px;height:4032px;overflow:hidden}
body{font-family:"Montserrat",sans-serif;color:var(--text);position:relative;background:var(--white)}
.abs{position:absolute}
section{position:absolute;left:0;width:1200px;overflow:hidden}

/* Hero */
.hero{top:0;height:696px;background:linear-gradient(135deg,#26b4bc 0%,#1fa9b2 100%)}
.brand{left:133px;top:14px;display:flex;align-items:center;gap:8px;color:var(--navy);font-weight:800;font-size:28px}
.brand .dot{width:30px;height:30px;border-radius:50%;background:var(--orange)}
.nav{top:26px;left:0;width:1200px;height:20px}
.nav a{position:absolute;color:var(--white);font-size:12px;font-weight:500;text-decoration:none;letter-spacing:.5px}
.hero-circle{left:566px;top:104px;width:740px;height:740px;border-radius:50%;background:var(--orange)}
.hero-photo{left:640px;top:88px;width:560px;height:608px;border-radius:280px 0 0 0;background:linear-gradient(180deg,#b97a52 0%,#a5653f 45%,#2aa6a6 100%)}
.hero-title{left:128px;top:172px;color:var(--white);font-size:42px;font-weight:600;letter-spacing:.3px}
.hero-sub{left:128px;top:232px;width:540px;color:var(--white);font-size:22px;font-weight:300;line-height:32px}
.hero-chart{left:124px;top:390px}
.checks{left:402px;top:358px;list-style:none}
.checks li{display:flex;align-items:center;gap:9px;color:var(--white);font-size:14px;font-weight:600;height:35.5px}
.checks svg{flex:none}

/* Awards */
.awards{top:696px;height:86px;background:var(--teal-light)}
.award{top:0;height:86px;display:flex;align-items:center;gap:12px;color:var(--white);font-size:10px;font-weight:700;line-height:15px}
.award span:last-child{width:260px}
.award .badge{flex:none;width:40px;height:40px;border:2px solid var(--white);border-radius:50%}
.award .badge.square{border-radius:4px;width:32px}
.awards .divider{top:10px;width:1px;height:66px;background:rgba(255,255,255,.5)}

/* How it works */
.how{top:782px;height:540px;background:var(--white)}
.section-title{left:0;width:1200px;text-align:center;font-size:26px;font-weight:700;color:var(--navy)}
.step-card{top:175px;width:307px;height:291px;border:1px solid var(--line);padding:66px 30px 0 50px}
.step-badge{top:125px;width:94px;height:94px;border-radius:50%;border:5px solid #e5eced;display:flex;flex-direction:column;align-items:center;justify-content:center;color:var(--white)}
.step-badge small{font-size:15px;font-weight:500;line-height:16px}
.step-badge b{font-size:22px;font-weight:800;line-height:24px}
.step-badge.gray{background:#b8bdc0}
.step-badge.orange{background:var(--orange)}
.step-badge.teal{background:var(--teal)}
.step-card h3{color:var(--teal);font-size:13px;font-weight:700;text-align:center;margin-left:-20px}
.step-card h4{margin-top:14px;border-left:2px solid var(--navy);padding-left:9px;font-size:9.5px;font-weight:600;color:var(--navy);line-height:13px}
.step-card p{margin-top:14px;font-size:10px;line-height:15px;color:var(--text)}
.step-card .row{display:flex;gap:12px;margin-top:10px;font-size:10px;line-height:14px}
.step-card .row i{flex:none;width:16px;height:16px;border:1.5px solid var(--muted);border-radius:3px}

/* Customizable */
.custom{top:1322px;height:527px;background:linear-gradient(160deg,#29bfc5 0%,#1caab3 60%,#22b5bc 100%)}
.custom .section-title{color:var(--white);top:56px}
.custom-lead{top:122px;left:170px;width:860px;text-align:center;color:var(--white);font-size:13px;line-height:24px}
.pill{top:211px;height:219px;background:var(--white);border-radius:110px}
.pill h3{color:var(--teal-dark);font-size:16px;font-weight:700;line-height:21px}
.pill p{font-size:11px;line-height:21px;color:var(--text)}
.pill .ph{border-radius:50% 45% 50% 48%}

/* Customers */
.clients{top:1849px;height:529px;background:var(--white)}
.clients .section-title{top:103px;font-size:24px}
.clients .section-title em{font-style:normal;color:var(--orange)}
.rule{height:3px;width:44px;background:var(--orange)}
.client{transform:translateX(-50%);display:flex;align-items:center;gap:8px;color:var(--navy);font-size:21px;font-weight:700;white-space:nowrap}
.client i{width:22px;height:22px;background:var(--navy);flex:none}

/* Success */
.success{top:2378px;height:482px;background:linear-gradient(180deg,#1fb0b8 0%,#26bac1 100%)}
.success .section-title{top:63px;color:var(--white)}
.story{top:144px;width:440px;height:249px;border:2px solid rgba(255,255,255,.85);text-align:center;color:var(--white)}
.story .name{margin-top:32px;display:flex;justify-content:center;align-items:center;gap:10px;font-size:28px;font-weight:700}
.story .name i{width:32px;height:32px;border-radius:50%;border:2px solid var(--white)}
.story blockquote{margin:18px auto 0;width:360px;font-size:14px;line-height:23px}
.story blockquote b{font-size:24px;font-family:Georgia,serif;vertical-align:-6px}
.btn{display:inline-block;background:var(--orange);color:var(--white);font-weight:600;border-radius:20px;text-decoration:none}
.story .btn{margin-top:16px;width:141px;height:34px;line-height:34px;font-size:12px}
.arrow{top:250px}

/* Contact */
.contact{top:2860px;height:637px;background:linear-gradient(180deg,#1e4d57 0%,#1a5a63 50%,#123f47 100%)}
.contact .section-title{top:98px;color:var(--white)}
.field{background:var(--white);border:1px solid #c9d4d8;height:55px;padding-left:22px;display:flex;align-items:center;color:#9aa3a8;font-size:14px}
.field.msg{align-items:flex-start;padding-top:18px}
.submit{left:513px;top:512px;width:191px;height:54px;line-height:54px;text-align:center;font-size:17px;border-radius:27px}

/* Footer */
.footer{top:3497px;height:469px;background:var(--white)}
.footer h5{font-size:13px;font-weight:700;color:var(--navy);letter-spacing:.3px}
.footer .small{font-size:12px;line-height:21px;color:var(--text)}
.footer .small b{font-weight:700;color:var(--navy)}
.search{width:214px;height:31px;border:1px solid #c7cfd3;display:flex;align-items:center;justify-content:space-between;padding:0 8px;font-size:11px;color:var(--muted)}
.social{display:flex;align-items:center;gap:12px;font-size:12px;color:var(--text);height:47px}
.social i{width:34px;height:34px;border-radius:50%;background:var(--teal)}
.links{list-style:none}
.links li{font-size:12px;color:var(--text);height:30px}
.select{width:143px;height:31px;border:1px solid #c7cfd3;display:flex;align-items:center;justify-content:space-between;padding:0 10px;font-size:11px;color:var(--text)}
.footer-brand{display:flex;align-items:center;gap:8px;color:var(--navy);font-size:26px;font-weight:800}
.footer-brand i{width:32px;height:32px;border-radius:50%;background:var(--orange)}
.copy{position:absolute;left:0;top:3966px;width:1200px;height:66px;background:var(--footer-bar);text-align:center;line-height:66px;font-size:12px;color:var(--text)}
</style>
</head>
<body>

<section class="hero">
  <div class="abs hero-circle"></div>
  <div class="abs hero-photo" role="img" aria-label="Woman in a hero cape with a brick-wall shirt, hands on hips"></div>

  <div class="abs brand"><span class="dot"></span>Veltomar</div>
  <nav class="abs nav">
    <a style="left:546px">HOME</a>
    <a style="left:651px">SOLUTION</a>
    <a style="left:783px">PRICING</a>
    <a style="left:901px">ABOUT</a>
    <a style="left:1012px">CONTACT</a>
  </nav>

  <h1 class="abs hero-title">HUMAN FIREWALL</h1>
  <p class="abs hero-sub">Mittels Cyber Awareness Schulungen das Risiko von Attacken innerhalb von 12 Monaten messbar um 50% senken</p>

  <svg class="abs hero-chart" width="420" height="260" viewBox="0 0 420 260">
    <g stroke="#fff" stroke-width="1.5" fill="none">
      <line x1="20" y1="0" x2="20" y2="226"/>
      <line x1="20" y1="226" x2="370" y2="226"/>
    </g>
    <text x="12" y="40" fill="#fff" font-size="10" font-family="Montserrat, sans-serif" transform="rotate(-90 12 40)">RISK</text>
    <text x="374" y="230" fill="#fff" font-size="10" font-family="Montserrat, sans-serif">TIME</text>
    <g fill="#d4f1f2" opacity=".85">
      <rect x="40" y="20" width="58" height="206"/>
      <rect x="123" y="90" width="58" height="136"/>
      <rect x="200" y="138" width="56" height="88"/>
      <rect x="276" y="176" width="57" height="50"/>
    </g>
    <g fill="#fff" font-size="8.5" font-weight="700" font-family="Montserrat, sans-serif" text-anchor="middle">
      <text x="69" y="242">GENERIC</text><text x="69" y="252">TRAINING</text>
      <text x="152" y="242">ATTACK</text><text x="152" y="252">SIMULATION</text>
      <text x="228" y="242">SECURITY</text><text x="228" y="252">GAME</text>
      <text x="304" y="242">ROLE BASED</text><text x="304" y="252">TRAINING</text>
    </g>
  </svg>

  <ul class="abs checks">
    <li><svg width="17" height="17" viewBox="0 0 17 17"><circle cx="8.5" cy="8.5" r="8.5" fill="#fff"/><path d="M4.5 8.8l2.7 2.6 5-5" stroke="var(--teal)" stroke-width="2" fill="none"/></svg>Mit Geld Zuruck Garantie!</li>
    <li><svg width="17" height="17" viewBox="0 0 17 17"><circle cx="8.5" cy="8.5" r="8.5" fill="#fff"/><path d="M4.5 8.8l2.7 2.6 5-5" stroke="var(--teal)" stroke-width="2" fill="none"/></svg>Individualisierbare Inhalte</li>
    <li><svg width="17" height="17" viewBox="0 0 17 17"><circle cx="8.5" cy="8.5" r="8.5" fill="#fff"/><path d="M4.5 8.8l2.7 2.6 5-5" stroke="var(--teal)" stroke-width="2" fill="none"/></svg>Preiswerte Losung</li>
    <li><svg width="17" height="17" viewBox="0 0 17 17"><circle cx="8.5" cy="8.5" r="8.5" fill="#fff"/><path d="M4.5 8.8l2.7 2.6 5-5" stroke="var(--teal)" stroke-width="2" fill="none"/></svg>Datenschutzkonform</li>
  </ul>
</section>

<section class="awards">
  <div class="abs award" style="left:112px"><span class="badge square"></span><span>In 2020, VELTOMAR won the Digital Guard Merit Award for Best Anti Phishing</span></div>
  <div class="abs divider" style="left:402px"></div>
  <div class="abs award" style="left:422px"><span class="badge"></span><span>In 2020, VELTOMAR won the Digital Guard Merit Award for the Best "Security Education Platform"</span></div>
  <div class="abs divider" style="left:782px"></div>
  <div class="abs award" style="left:800px"><span class="badge"></span><span>2020 Gold Winner "Cyber Security Education and Training" in the SecureTech Review</span></div>
</section>

<section class="how">
  <h2 class="abs section-title" style="top:62px">HOW DOES IT WORK?</h2>

  <div class="abs step-card" style="left:128px">
    <h3>SET GOALS &amp; CREATE A PLAN</h3>
    <h4>UNDERSTNDING YOUR GOALS WILL<br>DEFINE PROGRAM SCOPE</h4>
    <p>Lorem Ipsum is simply dummy text of the printing and typesetting industry. Lorem Ipsum</p>
    <div class="row"><i></i><span>Lorem Ipsum is simply dummy text of the printing and typesetting industry.</span></div>
    <div class="row"><i></i><span>Lorem Ipsum is simply dummy text of the printing and typesetting industry.</span></div>
  </div>
  <div class="abs step-badge gray" style="left:231px"><small>STEP</small><b>Nº1</b></div>

  <div class="abs step-card" style="left:451px">
    <h3>ASSESS AWEARENESS LEVEL</h3>
    <h4>USE PHISHING SIMULATIONS OR ASSESSMENTS TO UNDERTAND THE CURRENT AWARENESS LEVEL</h4>
    <p>Lorem Ipsum is simply dummy text of the printing and typesetting industry. Lorem Ipsum</p>
    <div class="row"><i></i><span>Lorem Ipsum is simply dummy text of the printing and typesetting industry.</span></div>
    <div class="row"><i></i><span>Lorem Ipsum is simply dummy text of the printing and typesetting industry.</span></div>
  </div>
  <div class="abs step-badge orange" style="left:553px"><small>STEP</small><b>Nº2</b></div>

  <div class="abs step-card" style="left:773px">
    <h3>RUN THE AWARENESS CAMPAIGN</h3>
    <h4>IMPROVE THE SECURITY AWARENESS LEVEL WITH TAILORED CORSES. OPTIMIZE THE PROGRAM OVER TIME</h4>
    <p>Lorem Ipsum is simply dummy text of the printing and typesetting industry.</p>
    <div class="row"><i></i><span>Lorem Ipsum is simply dummy text of the printing and typesetting industry.</span></div>
    <div class="row"><i></i><span>Lorem Ipsum is simply dummy text of the printing and typesetting industry.</span></div>
  </div>
  <div class="abs step-badge teal" style="left:886px"><small>STEP</small><b>Nº3</b></div>
</section>

<section class="custom">
  <h2 class="abs section-title">FULLY CUSTOMIZABLE!</h2>
  <p class="abs custom-lead">You Might Ask: WHy do the Trainings need customization? In &nbsp;Addition to adjusting the design (Logo, Font, Colors) to Your Corporate Look and feel, It is Important that your emploees perceive the training as soemthing they can relate to.<br>EXAMPLES:</p>

  <div class="abs pill" style="left:89px;width:502px">
    <h3 class="abs" style="left:71px;top:56px">FROM CEO:</h3>
    <p class="abs" style="left:71px;top:88px;width:195px">Add a personal greeting message from your CEO at the start of the course to highlight the importance of the training.</p>
    <div class="abs ph" style="left:290px;top:36px;width:181px;height:149px;background:linear-gradient(135deg,#e9e7e4 0%,#b9b4ae 55%,#6f6a66 100%)" role="img" aria-label="Laptop on a desk showing a video greeting from a company executive"></div>
  </div>

  <div class="abs pill" style="left:605px;width:504px">
    <div class="abs" style="left:52px;top:44px;width:188px;height:131px;background:linear-gradient(180deg,#f3f4f5 0%,#e2e5e7 100%);border:1px solid #d4d8db" role="img" aria-label="Screenshot of a policy acknowledgement page in the training portal"></div>
    <h3 class="abs" style="left:266px;top:52px;width:200px">DO YOU KNOW OUR POLICIES?</h3>
    <p class="abs" style="left:266px;top:105px;width:205px">You could ask the user to read and acknowledge your internal policies prior to starting the course.</p>
  </div>
</section>

<section class="clients">
  <h2 class="abs section-title">MEHR ALS <em>400</em> KUNDEN VERTRAUEN BEREITS AUF VELTOMAR:</h2>
  <div class="abs rule" style="left:584px;top:141px"></div>

  <div class="abs client" style="left:227px;top:222px">ALPENFLUG</div>
  <div class="abs client" style="left:468px;top:222px">Kessler Informatik</div>
  <div class="abs client" style="left:704px;top:222px"><span style="font-size:15px;line-height:18px">Nordhafen<br>Stadtwerke</span><i style="width:40px;height:40px"></i></div>
  <div class="abs client" style="left:901px;top:222px">Railfracht</div>
  <div class="abs client" style="left:1045px;top:222px">Corvia</div>

  <div class="abs client" style="left:291px;top:352px">MUHLWERK</div>
  <div class="abs client" style="left:491px;top:352px">CALDERON</div>
  <div class="abs client" style="left:706px;top:352px">Hausmobil</div>
  <div class="abs client" style="left:900px;top:352px"><i style="border-radius:50%"></i>FERRANT</div>
</section>

<section class="success">
  <h2 class="abs section-title">SUCCESS STORIES</h2>
  <svg class="abs arrow" style="left:78px" width="22" height="38" viewBox="0 0 22 38"><path d="M19 3L4 19l15 16" stroke="#fff" stroke-width="3.5" fill="none"/></svg>
  <svg class="abs arrow" style="left:1097px" width="22" height="38" viewBox="0 0 22 38"><path d="M3 3l15 16L3 35" stroke="#fff" stroke-width="3.5" fill="none"/></svg>

  <div class="abs story" style="left:147px">
    <div class="name"><i></i>Skyvara</div>
    <blockquote><b>“</b> Veltomar bietet ein optimales Gesamtpaket, mit dem wir die Awareness bei unseren Mitarbeitern dauehaft hochhalten konnen <b>”</b></blockquote>
    <a class="btn">Read More</a>
  </div>
  <div class="abs story" style="left:620px">
    <div class="name"><i style="border-radius:4px"></i>Nordkost</div>
    <blockquote><b>“</b> Es ist einfach ein tolles Gefuhl, wenn man sieht, dass die Mitarbeiter deutlich wachsamer geworden sind <b>”</b></blockquote>
    <a class="btn">Read More</a>
  </div>
</section>

<section class="contact" role="img" aria-label="Team of colleagues at work behind a dark teal overlay">
  <h2 class="abs section-title">GET IN TOUCH WITH US</h2>
  <div class="abs rule" style="left:578px;top:140px"></div>
  <div class="abs field" style="left:133px;top:175px;width:462px">Full Name*</div>
  <div class="abs field" style="left:610px;top:175px;width:463px">Your Email*</div>
  <div class="abs field" style="left:133px;top:245px;width:462px">Phone</div>
  <div class="abs field" style="left:610px;top:245px;width:463px">Subject*</div>
  <div class="abs field" style="left:133px;top:313px;width:462px">Country</div>
  <div class="abs field" style="left:610px;top:313px;width:463px">Location</div>
  <div class="abs field msg" style="left:133px;top:382px;width:940px;height:114px">Message*</div>
  <a class="abs btn submit">Submit &rsaquo;</a>
</section>

<section class="footer">
  <div class="abs" style="left:124px;top:74px">
    <h5>CONTACTS</h5>
    <div class="small" style="margin-top:14px">
      <b>Address: Europe</b><br>Veltomar Security AG Lindenweg 17<br>6410 Arlenbach Switzerland<br><br>
      <b>Address: North America</b><br>Veltomar Security USA 4820 Meridian Ave<br>Suite 310 Dalton, TX 75900<br><br>
      Phone Global: +41 40 555 01 23<br>Phone USA: +1-555-010-4410<br>Phone USA Support: +1-555-010-4420<br>Phone Canand: +1 555-010-7788<br>Phone France: +33 655 501 020<br>Phone UK: +44(0) 7555 010345
    </div>
  </div>

  <div class="abs" style="left:446px;top:78px">
    <h5>SEARCH</h5>
    <div class="search" style="margin-top:14px">Search
      <svg width="14" height="14" viewBox="0 0 14 14"><circle cx="6" cy="6" r="4.5" stroke="var(--teal)" stroke-width="2" fill="none"/><path d="M9.5 9.5L13 13" stroke="var(--teal)" stroke-width="2"/></svg>
    </div>
    <h5 style="margin-top:40px">CONNECT</h5>
    <div style="margin-top:10px">
      <div class="social"><i></i>Friendwall</div>
      <div class="social"><i></i>Chirper</div>
      <div class="social"><i></i>Viewcast</div>
      <div class="social"><i></i>Worknet</div>
    </div>
  </div>

  <div class="abs" style="left:743px;top:80px">
    <h5>INFOMATION</h5>
    <ul class="links" style="margin-top:18px">
      <li>Home</li><li>Solution</li><li>Pricing</li><li>Resources</li><li>About Us</li><li>Support Wiki</li><li>Contact</li><li>Download VELTOMAR</li><li>Demo Request</li>
    </ul>
  </div>

  <div class="abs" style="left:937px;top:78px">
    <h5>LANGUAGE</h5>
    <div class="select" style="margin-top:14px">English
      <svg width="10" height="6" viewBox="0 0 10 6"><path d="M0 0h10L5 6z" fill="var(--navy)"/></svg>
    </div>
    <div class="footer-brand" style="margin-top:42px"><i></i>Veltomar</div>
  </div>
</section>

<div class="copy">© Veltomar All Rights Reserved 2021</div>

</body>
</html>
```